Water ATM Card

Need a design for water ATM cards. Size of card is 3.375 x 2.125 inch
On the Front include the Cedar hollow Logo.
Bottom right corner should have Price $100
On the Back
This card is to be used to access water refills at any Cedar Hollow Water Vending Machines.
Please contact (869) 418 2930 or (869) 534 1276 or email clearflowbox@mailvista.example for any assistance or recharging of card.

```html
<!DOCTYPE html>
<html lang="en">
<head>
<meta charset="utf-8">
<title>Cedar Hollow Water Card</title>
<link href="https://fonts.googleapis.com/css2?family=Montserrat:wght@500;800&family=Advent+Pro:wght@200&display=swap" rel="stylesheet">
<style>
  :root {
    --backdrop: #222222;
    --card: #151515;
    --brand-blue: #0a78c2;
    --price-green: #3aa64a;
    --body-text: #c9ced3;
  }
  * { box-sizing: border-box; margin: 0; padding: 0; }
  html, body {
    width: 1200px;
    height: 711px;
    overflow: hidden;
    background: var(--backdrop);
  }
  .canvas {
    position: relative;
    width: 1200px;
    height: 711px;
    display: flex;
    align-items: center;
    justify-content: center;
    gap: 60px;
  }
  .card {
    position: relative;
    width: 480px;
    height: 302px;
    background: var(--card);
    border-radius: 18px;
    box-shadow: 0 6px 18px rgba(0, 0, 0, 0.55);
  }
  .brand {
    position: absolute;
    left: 0;
    right: 0;
    top: 118px;
    display: flex;
    align-items: center;
    justify-content: center;
    gap: 12px;
  }
  .brand-mark {
    width: 22px;
    height: 22px;
    border-radius: 50%;
    background: var(--brand-blue);
  }
  .brand-name {
    font-family: "Montserrat", sans-serif;
    font-weight: 800;
    font-size: 36px;
    letter-spacing: 1px;
    text-transform: uppercase;
    color: var(--brand-blue);
  }
  .card-back .brand {
    top: 34px;
    gap: 10px;
  }
  .card-back .brand-mark {
    width: 16px;
    height: 16px;
  }
  .card-back .brand-name {
    font-size: 26px;
  }
  .back-info {
    position: absolute;
    left: 36px;
    right: 36px;
    top: 92px;
    font-family: "Montserrat", sans-serif;
    font-weight: 500;
    font-size: 13px;
    line-height: 1.55;
    color: var(--body-text);
    text-align: center;
  }
  .back-info p + p {
    margin-top: 12px;
  }
  .contact-list {
    margin-top: 14px;
    list-style: none;
    font-size: 14px;
    line-height: 1.7;
    color: var(--brand-blue);
  }
  .price {
    position: absolute;
    right: 30px;
    bottom: 26px;
    font-family: "Advent Pro", sans-serif;
    font-weight: 200;
    font-size: 40px;
    letter-spacing: 0.5px;
    color: var(--price-green);
  }
</style>
</head>
<body>
  <main class="canvas">
    <section class="card card-back">
      <div class="brand">
        <span class="brand-mark"></span>
        <span class="brand-name">Cedar Hollow</span>
      </div>
      <div class="back-info">
        <p>This card is to be used to access water refills at any Cedar Hollow Water Vending Machines.</p>
        <p>Please contact us for any assistance or recharging of card.</p>
        <ul class="contact-list">
          <li>(869) 418 2930 &nbsp;|&nbsp; (869) 534 1276</li>
          <li>clearflowbox@mailvista.example</li>
        </ul>
      </div>
    </section>
    <section class="card card-front">
      <div class="brand">
        <span class="brand-mark"></span>
        <span class="brand-name">Cedar Hollow</span>
      </div>
      <p class="price">PRICE $100</p>
    </section>
  </main>
</body>
</html>
```